Modern Business Card

Modern professional business card with more than just logo and demographic info. Something memorable.

We are a trendy/modern chiropractic group with an emphasis on neurology, hence the minimalist-type brain logo. We want to convey that modern and technical aspect with professionalism and the elite nature of our practice environment.

```html
<!DOCTYPE html>
<html lang="en">
<head>
<meta charset="utf-8">
<title>Meridian Spine Studio — Business Card</title>
<link href="https://fonts.googleapis.com/css2?family=Open+Sans:wght@400;600;700&display=swap" rel="stylesheet">
<style>
  :root {
    --backdrop: #3b322d;
    --card-dark: #1f2023;
    --card-dark-ink: #36373c;
    --card-light: #fbfbfa;
    --brand-blue: #2b6cc4;
    --ink: #3a3a3a;
    --ink-soft: #555;
  }
  * { box-sizing: border-box; margin: 0; padding: 0; }
  html, body {
    width: 1200px; height: 847px; overflow: hidden;
    background: var(--backdrop);
    font-family: "Open Sans", sans-serif;
  }
  .canvas { position: relative; width: 1200px; height: 847px; }

  .card {
    position: absolute;
    width: 520px; height: 297px;
    border-radius: 3px;
  }

  /* Front: dark side, shown as a stack with blue painted edges */
  .card--front {
    left: 70px; top: 100px;
    background: var(--card-dark);
    overflow: hidden;
    box-shadow:
      0 3px 0 var(--brand-blue),
      0 5px 0 var(--card-dark),
      0 8px 0 var(--brand-blue),
      0 10px 0 var(--card-dark),
      0 13px 0 var(--brand-blue),
      0 15px 0 var(--card-dark),
      0 18px 0 var(--brand-blue),
      0 26px 30px rgba(0,0,0,.45);
  }
  .card--front .emboss-field {
    position: absolute; left: 40px; top: 30px;
    width: 300px; height: 190px;
    border-radius: 40px;
    background: radial-gradient(ellipse at 35% 45%, #3a3b40 0%, #2a2b2f 45%, rgba(31,32,35,0) 75%);
  }
  .card--front .wordmark {
    position: absolute; right: 34px; bottom: 30px;
    font-weight: 700; font-size: 32px; line-height: 1.05;
    color: var(--card-dark-ink);
    text-transform: uppercase; text-align: right;
    letter-spacing: 1px;
  }

  /* Back: white side */
  .card--back {
    left: 610px; top: 430px;
    background: var(--card-light);
    border-bottom: 4px solid var(--brand-blue);
    box-shadow: 0 12px 26px rgba(0,0,0,.4);
    display: flex; align-items: center;
    padding: 0 26px;
  }
  .brand {
    display: flex; align-items: center; gap: 10px;
    width: 226px;
  }
  .brand__mark {
    width: 18px; height: 18px; flex: none;
    background: var(--brand-blue);
  }
  .brand__name {
    font-weight: 700; font-size: 21px; line-height: 1.05;
    color: #222; text-transform: uppercase; letter-spacing: .5px;
  }
  .divider {
    width: 2px; height: 150px; background: var(--brand-blue);
    margin: 0 16px 0 8px; flex: none;
  }
  .contact { color: var(--ink); font-size: 14px; line-height: 1.4; white-space: nowrap; }
  .contact__name {
    font-weight: 700; font-size: 19px; color: var(--brand-blue);
    text-transform: uppercase; letter-spacing: .5px; line-height: 1.1;
  }
  .contact__role { color: var(--ink-soft); margin-bottom: 6px; }
  .contact__address { margin-bottom: 6px; }
  .contact__line { display: flex; align-items: center; gap: 6px; }
  .contact__line svg { width: 12px; height: 12px; fill: var(--brand-blue); flex: none; }
</style>
</head>
<body>
<main class="canvas">

  <section class="card card--front" aria-label="Card front">
    <div class="emboss-field" role="img" aria-label="Large glossy embossed brand pattern"></div>
    <div class="wordmark">Meridian<br>Spine Studio</div>
  </section>

  <section class="card card--back" aria-label="Card back">
    <div class="brand">
      <span class="brand__mark"></span>
      <span class="brand__name">Meridian<br>Spine Studio</span>
    </div>
    <div class="divider"></div>
    <div class="contact">
      <p class="contact__name">Daniel Rourke</p>
      <p class="contact__role">President</p>
      <p class="contact__address">1180 Harbor Crest Way<br>Seacliff CA 92000</p>
      <p class="contact__line">
        <svg viewBox="0 0 24 24" aria-hidden="true"><path d="M6.6 10.8a15.1 15.1 0 0 0 6.6 6.6l2.2-2.2a1 1 0 0 1 1-.25 11.4 11.4 0 0 0 3.6.57 1 1 0 0 1 1 1V20a1 1 0 0 1-1 1A17 17 0 0 1 3 4a1 1 0 0 1 1-1h3.5a1 1 0 0 1 1 1c0 1.25.2 2.46.57 3.58a1 1 0 0 1-.25 1z"/></svg>
        555-014-2290
      </p>
      <p class="contact__line">
        <svg viewBox="0 0 24 24" aria-hidden="true"><path d="M2 5h20v14H2z M2 5l10 8 10-8" fill="none" stroke="#2b6cc4" stroke-width="2"/></svg>
        daniel@meridianspine.com
      </p>
      <p class="contact__line">
        <svg viewBox="0 0 24 24" aria-hidden="true"><circle cx="12" cy="12" r="10"/><path d="M2 12h20M12 2c3 3 3 17 0 20M12 2c-3 3-3 17 0 20" fill="none" stroke="#fff" stroke-width="1.4"/></svg>
        www.meridianspine.com
      </p>
    </div>
  </section>

</main>
</body>
</html>
```